Wordpress Template Design using existing Logo and Colors

We are wanting a wordpress theme designing for our b2b marketing consultancy business. A comprehesive and elagant design to our current site www.plovtrix.com would be good.

Industry/Entity Type

Marketing

Font styles to use
Sans Serif

```html
<!DOCTYPE html>
<html lang="en">
<head>
<meta charset="utf-8">
<title>PLOVTRIX – B2B Marketing Consultancy</title>
<link href="https://fonts.googleapis.com/css2?family=Open+Sans:wght@400;600;700;800&family=Roboto:wght@400;500;700;900&display=swap" rel="stylesheet">
<style>
:root{
  --red:#e3161f;
  --dark:#1b1c1e;
  --darker:#111213;
  --text:#555b61;
  --heading:#2b2e33;
  --light:#f3f4f5;
  --white:#ffffff;
  --slate1:#3b4654;
  --slate2:#5d6b7b;
}
*{box-sizing:border-box;margin:0;padding:0}
html,body{width:1200px;height:2236px;overflow:hidden}
body{font-family:"Open Sans",Arial,sans-serif;color:var(--text);background:var(--white);position:relative}
.hero{position:absolute;left:0;top:0;width:1200px;height:560px;overflow:hidden}
.hero-photo{position:absolute;inset:0;background:linear-gradient(180deg,#8da0b4 0%,#5d7290 35%,#2f3f56 62%,#4a5a6e 78%,#20262f 100%)}
.hero-shade{position:absolute;inset:0;background:rgba(10,14,22,.25)}
.site-header{position:absolute;left:0;top:0;width:1200px;height:72px;background:rgba(10,12,16,.55);display:flex;align-items:center;padding:0 100px}
.brand{font-family:"Roboto",sans-serif;font-weight:900;font-size:34px;color:var(--white);letter-spacing:1px;display:flex;align-items:center;gap:10px}
.brand-dot{width:12px;height:12px;background:var(--red);border-radius:50%}
.main-nav{margin-left:auto;display:flex;align-items:center;gap:34px;font-family:"Roboto",sans-serif;font-size:16px;font-weight:500;color:var(--white);text-transform:uppercase}
.main-nav .active{color:var(--red)}
.hero-copy{position:absolute;left:0;right:0;top:262px;text-align:center;color:var(--white)}
.hero-title{font-family:"Roboto",sans-serif;font-weight:900;font-size:76px;letter-spacing:2px;line-height:1.1}
.hero-sub{font-size:28px;margin-top:8px}
.btn-outline{display:inline-block;margin-top:28px;border:2px solid var(--white);border-radius:30px;padding:12px 36px;font-size:18px;font-weight:700;text-transform:uppercase}
.hero-dots{position:absolute;top:504px;left:0;right:0;display:flex;justify-content:center;gap:8px}
.hero-dots span{width:12px;height:12px;border-radius:50%;background:rgba(255,255,255,.5)}
.hero-dots span:first-child{background:var(--white)}
.welcome{position:absolute;top:560px;left:0;width:1200px;height:440px;background:var(--white)}
.welcome h2{position:absolute;left:100px;top:100px;font-family:"Roboto",sans-serif;font-weight:900;font-size:38px;line-height:46px;color:var(--heading)}
.welcome-text{position:absolute;left:100px;top:166px;width:470px;font-size:14px;line-height:22px}
.welcome-text p+p{margin-top:16px}
.btn-red{display:inline-block;background:var(--red);color:var(--white);border-radius:30px;font-weight:700;text-transform:uppercase}
.welcome .btn-red{position:absolute;left:100px;top:340px;padding:11px 26px;font-size:14px}
.welcome-media{position:absolute;left:616px;top:80px;width:444px;height:290px;border:6px solid var(--white);box-shadow:0 2px 12px rgba(0,0,0,.25);background:linear-gradient(135deg,#e8edf3,#b9c6d4 55%,#6f8296)}
.play{position:absolute;left:50%;top:50%;width:64px;height:64px;margin:-32px 0 0 -32px}
.services{position:absolute;top:1000px;left:0;width:1200px;height:520px;background:linear-gradient(135deg,var(--slate1),var(--slate2) 60%,var(--slate1))}
.services h2{position:absolute;top:64px;left:0;right:0;text-align:center;font-family:"Roboto",sans-serif;font-weight:900;font-size:48px;color:var(--white)}
.service-grid{position:absolute;top:192px;left:100px;display:flex;gap:28px}
.service-card{width:229px;height:288px;border:2px solid rgba(255,255,255,.85);text-align:center;color:var(--white);padding-top:70px;position:relative}
.service-icon{position:absolute;top:-40px;left:50%;margin-left:-40px;width:80px;height:80px;border-radius:50%;background:var(--white)}
.service-card h3{font-family:"Roboto",sans-serif;font-size:18px;font-weight:700;text-transform:uppercase}
.service-card p{font-size:14px;line-height:22px;padding:16px 22px 0}
.brochure{position:absolute;top:1520px;left:0;width:1200px;height:400px;background:var(--light);text-align:center}
.brochure h2{padding-top:88px;font-family:"Roboto",sans-serif;font-weight:900;font-size:42px;color:var(--heading)}
.brochure p{width:620px;margin:16px auto 0;font-size:16px;line-height:24px}
.brochure .btn-red{margin-top:28px;padding:14px 34px;font-size:17px}
.footer{position:absolute;top:1920px;left:0;width:1200px;height:260px;background:var(--dark);color:#c9ccd0}
.footer .brand{position:absolute;left:100px;top:100px;font-size:32px}
.footer-col{position:absolute;top:40px;font-size:13px;line-height:21px}
.footer-col h4{font-family:"Roboto",sans-serif;color:var(--white);font-size:16px;font-weight:700;text-transform:uppercase;margin-bottom:14px}
.links{left:400px}.news{left:600px;width:230px}.contact{left:880px;width:240px}
.news input{display:block;width:200px;height:30px;margin:12px 0 10px;border:0;padding:0 10px;font-size:12px;background:var(--white)}
.news .btn-red{padding:5px 16px;font-size:11px}
.contact li{list-style:none;display:flex;gap:10px;align-items:flex-start;margin-bottom:6px}
.contact svg{flex:none;margin-top:4px}
.bottom-bar{position:absolute;top:2180px;left:0;width:1200px;height:56px;background:var(--darker);color:#9ea3a8;font-size:12px;display:flex;align-items:center;padding:0 100px}
.social{margin-left:auto;display:flex;gap:8px}
.social span{width:26px;height:26px;border-radius:50%;border:1px solid #9ea3a8}
</style>
</head>
<body>
<section class="hero">
  <div class="hero-photo" role="img" aria-label="City skyline at dusk reflected in a harbour"></div>
  <div class="hero-shade"></div>
  <header class="site-header">
    <div class="brand"><span class="brand-dot"></span>PLOVTRIX</div>
    <nav class="main-nav"><span class="active">Home</span><span>Target Marketing</span><span>Data Management</span><span>About</span>
      <svg width="18" height="18" viewBox="0 0 18 18"><circle cx="7.5" cy="7.5" r="5.5" fill="none" stroke="#fff" stroke-width="2"/><line x1="11.5" y1="11.5" x2="16" y2="16" stroke="#fff" stroke-width="2"/></svg>
    </nav>
  </header>
  <div class="hero-copy">
    <h1 class="hero-title">PLOVTRIX</h1>
    <p class="hero-sub">We are a b2b marketing consultancy business</p>
    <span class="btn-outline">Get more info!</span>
  </div>
  <div class="hero-dots"><span></span><span></span><span></span><span></span></div>
</section>

<section class="welcome">
  <h2>WELCOME TO PLOVTRIX</h2>
  <div class="welcome-text">
    <p>We are a B2B Data, Analytics and Marketing Consulting Company specialized in harnessing the power of proprietary data to strengthen connections between decision makers, companies and products.</p>
    <p>We focus on solutions engineered to solve distinct challenges in the data, direct marketing, and analytics space.</p>
  </div>
  <span class="btn-red">Read more</span>
  <div class="welcome-media" role="img" aria-label="Hands reviewing printed charts and reports on a desk">
    <svg class="play" viewBox="0 0 64 64"><circle cx="32" cy="32" r="30" fill="rgba(0,0,0,.55)" stroke="#fff" stroke-width="2"/><polygon points="26,20 46,32 26,44" fill="#fff"/></svg>
  </div>
</section>

<section class="services">
  <h2>SERVICES WE PROVIDE</h2>
  <div class="service-grid">
    <div class="service-card">
      <svg class="service-icon" viewBox="0 0 80 80"><circle cx="40" cy="40" r="40" fill="#fff"/><ellipse cx="40" cy="28" rx="14" ry="5" fill="#e3161f"/><path d="M26 28v24c0 3 6 5 14 5s14-2 14-5V28c0 3-6 5-14 5s-14-2-14-5z" fill="#e3161f"/></svg>
      <h3>B2B Database</h3>
      <p>Get access to the leading market and business intelligence database with 1,000,000 organisations and 2,000,000 decision makers.</p>
    </div>
    <div class="service-card">
      <svg class="service-icon" viewBox="0 0 80 80"><circle cx="40" cy="40" r="40" fill="#fff"/><polyline points="24,50 34,40 42,46 56,30" fill="none" stroke="#e3161f" stroke-width="4"/><polyline points="22,26 22,56 58,56" fill="none" stroke="#e3161f" stroke-width="3"/></svg>
      <h3>Target Marketing</h3>
      <p>Get access to the leading market and business intelligence database with 1,000,000 organisations and 2,000,000 decision makers.</p>
    </div>
    <div class="service-card">
      <svg class="service-icon" viewBox="0 0 80 80"><circle cx="40" cy="40" r="40" fill="#fff"/><path d="M24 44v-6a16 16 0 0 1 32 0v6" fill="none" stroke="#e3161f" stroke-width="4"/><rect x="21" y="42" width="8" height="12" rx="3" fill="#e3161f"/><rect x="51" y="42" width="8" height="12" rx="3" fill="#e3161f"/></svg>
      <h3>Call Centre</h3>
      <p>Get access to the leading market and business intelligence database with 1,000,000 organisations and 2,000,000 decision makers.</p>
    </div>
    <div class="service-card">
      <svg class="service-icon" viewBox="0 0 80 80"><circle cx="40" cy="40" r="40" fill="#fff"/><circle cx="40" cy="40" r="11" fill="none" stroke="#e3161f" stroke-width="7" stroke-dasharray="6 3"/><circle cx="40" cy="40" r="4" fill="#e3161f"/></svg>
      <h3>Data Management</h3>
      <p>Get access to the leading market and business intelligence database with 1,000,000 organisations and 2,000,000 decision makers.</p>
    </div>
  </div>
</section>

<section class="brochure">
  <h2>CORPORATE BROCHURE</h2>
  <p>Learn our leading target marketing and intelligent data management solutions to attract new customers for your entire products and services.</p>
  <span class="btn-red"><svg width="16" height="16" viewBox="0 0 16 16" style="vertical-align:-2px;margin-right:8px"><path d="M8 1v9M4 6l4 4 4-4M2 14h12" fill="none" stroke="#fff" stroke-width="2"/></svg>DOWNLOAD NOW</span>
</section>

<footer class="footer">
  <div class="brand"><span class="brand-dot"></span>PLOVTRIX</div>
  <div class="footer-col links">
    <h4>Quick Links</h4>
    B2B Database<br>Call Centre<br>Demand Generation<br>Lead Generation<br>Data Management<br>Marketing Automation<br>Data Append<br>Event Management
  </div>
  <div class="footer-col news">
    <h4>Newsletter Subscription</h4>
    Register your Email Address to get information about us.
    <input type="text" value="Enter Email" aria-label="Email address">
    <span class="btn-red">Subscribe</span>
  </div>
  <div class="footer-col contact">
    <h4>Contact Us</h4>
    <ul>
      <li><svg width="10" height="13" viewBox="0 0 10 13"><path d="M5 0a5 5 0 0 1 5 5c0 3-5 8-5 8S0 8 0 5a5 5 0 0 1 5-5z" fill="#c9ccd0"/><circle cx="5" cy="5" r="2" fill="#1b1c1e"/></svg>48 Harlow Street, Unit 5, Linden, NY 10021</li>
      <li><svg width="11" height="11" viewBox="0 0 11 11"><path d="M2 0l2 3-1 1.5a6 6 0 0 0 3.5 3.5L8 7l3 2-1 2C5 11 0 6 0 1z" fill="#c9ccd0"/></svg>+1 (555) 014-2290</li>
      <li><svg width="12" height="9" viewBox="0 0 12 9"><rect width="12" height="9" fill="#c9ccd0"/><path d="M0 0l6 5 6-5" fill="none" stroke="#1b1c1e"/></svg>contact@plovtrix.com</li>
      <li><svg width="11" height="11" viewBox="0 0 11 11"><circle cx="5.5" cy="5.5" r="5" fill="none" stroke="#c9ccd0"/><line x1="0.5" y1="5.5" x2="10.5" y2="5.5" stroke="#c9ccd0"/></svg>www.plovtrix.com</li>
    </ul>
  </div>
</footer>
<div class="bottom-bar">
  Copyright © 2016, PLOVTRIX. All rights reserved.
  <div class="social"><span></span><span></span><span></span><span></span></div>
</div>
</body>
</html>
```